Business Card Design Project

Company Name - Solvane Care

Wellness consulting and training company. Run through a medical centre.

Main colour themes are orange and blue, as in the logo. Want to replicate same effect with business cards.

To give a sense of freedom and potential as per the company name.

Want the business card to be in line with stationary design, which I have launched as well.

Double sided with design and colour on one side and details on other side.

Reason: Need business card and stationary design to be teed up.

Target Market(s)

35 to 65 age group.
New age and trendy

Industry/Entity Type

Training

Requirements
Must have
• Colours orange and blue as per logo
Nice to have
• Design to be similar to stationary design, letterhead and envelopes

```html
<!DOCTYPE html>
<html lang="en">
<head>
<meta charset="utf-8">
<title>Solvane Care — Business Card</title>
<link href="https://fonts.googleapis.com/css2?family=Lato:wght@400;700;900&display=swap" rel="stylesheet">
<style>
  :root {
    --stage: #e9e7e4;
    --card: #ffffff;
    --brand-blue: #2457a8;
    --brand-blue-light: #5b8fd0;
    --brand-orange: #f47c2a;
    --ink: #1c1c1c;
  }
  * { margin: 0; padding: 0; box-sizing: border-box; }
  html, body {
    width: 1200px;
    height: 900px;
    overflow: hidden;
    background: var(--stage);
    font-family: "Lato", Arial, sans-serif;
  }
  .stage {
    width: 1200px;
    height: 900px;
    display: flex;
    flex-direction: column;
    align-items: center;
    justify-content: center;
    gap: 40px;
  }
  .business-card {
    position: relative;
    width: 700px;
    height: 400px;
    background: var(--card);
    border-radius: 20px;
    box-shadow: 0 8px 24px rgba(0,0,0,0.12);
    flex: none;
  }

  /* Front: large brand face */
  .card-front {
    display: flex;
    align-items: center;
    justify-content: center;
    gap: 22px;
  }
  .front-dot {
    width: 30px;
    height: 30px;
    border-radius: 50%;
    background: var(--brand-orange);
    flex: none;
  }
  .front-name {
    font-weight: 400;
    font-size: 90px;
    letter-spacing: -1.5px;
    color: var(--brand-blue);
    line-height: 1;
    white-space: nowrap;
  }

  /* Back: details face */
  .brand {
    position: absolute;
    top: 86px;
    left: 0;
    right: 0;
    display: flex;
    align-items: center;
    justify-content: center;
    gap: 12px;
  }
  .brand-dot {
    width: 17px;
    height: 17px;
    border-radius: 50%;
    background: var(--brand-orange);
  }
  .brand-name {
    font-weight: 400;
    font-size: 50px;
    letter-spacing: -1px;
    color: var(--brand-blue);
    line-height: 1;
  }
  .details {
    position: absolute;
    top: 200px;
    left: 0;
    right: 0;
    display: flex;
    justify-content: center;
  }
  .identity {
    width: 290px;
    text-align: right;
    padding-right: 22px;
  }
  .person-name {
    font-weight: 900;
    font-size: 21px;
    color: var(--brand-blue);
    letter-spacing: 0.4px;
    line-height: 1.1;
  }
  .person-role {
    font-weight: 700;
    font-size: 16px;
    color: var(--brand-orange);
    margin-top: 2px;
  }
  .address {
    margin-top: 34px;
    font-weight: 700;
    font-size: 15px;
    line-height: 1.45;
    color: var(--ink);
    white-space: nowrap;
  }
  .divider {
    width: 3px;
    height: 118px;
    flex: none;
    background: linear-gradient(to bottom, rgba(91,143,208,0.1), var(--brand-blue-light) 40%, rgba(91,143,208,0));
  }
  .contacts {
    width: 290px;
    padding-left: 22px;
    list-style: none;
  }
  .contact-item {
    display: flex;
    align-items: center;
    gap: 10px;
    font-size: 15px;
    color: var(--ink);
    line-height: 1.6;
    white-space: nowrap;
  }
  .contact-icon {
    width: 17px;
    height: 17px;
    flex: none;
  }
  .website { font-weight: 900; }
  .website .domain { color: var(--brand-blue); }
</style>
</head>
<body>
<main class="stage">
  <article class="business-card card-front" aria-label="Card front">
    <span class="front-dot"></span>
    <span class="front-name">Solvane Care</span>
  </article>

  <article class="business-card card-back" aria-label="Card back">
    <header class="brand">
      <span class="brand-dot"></span>
      <span class="brand-name">Solvane Care</span>
    </header>

    <section class="details">
      <div class="identity">
        <p class="person-name">YOUR NAME</p>
        <p class="person-role">Centre Director</p>
        <p class="address">Via Lorenta Vasconi,<br>14 62010 Montelieve (MC), Italy</p>
      </div>

      <div class="divider"></div>

      <ul class="contacts">
        <li class="contact-item">
          <svg class="contact-icon" viewBox="0 0 24 24" aria-hidden="true">
            <path d="M3 9c0-3 4-5 9-5s9 2 9 5v1.5h-4.5V8.5c-1.4-.5-3-.7-4.5-.7s-3.1.2-4.5.7v2H3z" fill="var(--brand-blue)"/>
            <path d="M6 12h12l2 7H4z" fill="var(--brand-blue)"/>
            <circle cx="12" cy="15.5" r="2" fill="#fff"/>
          </svg>
          (+234) 555 0147
        </li>
        <li class="contact-item">
          <svg class="contact-icon" viewBox="0 0 24 24" aria-hidden="true">
            <rect x="6" y="3" width="12" height="18" rx="1.5" fill="none" stroke="var(--ink)" stroke-width="1.6"/>
          </svg>
          +39 300 5550182
        </li>
        <li class="contact-item">
          <svg class="contact-icon" viewBox="0 0 24 24" aria-hidden="true">
            <rect x="2" y="5" width="20" height="14" rx="1.5" fill="var(--brand-blue)"/>
            <path d="M3 6l9 7 9-7" fill="none" stroke="#fff" stroke-width="1.6"/>
          </svg>
          info@solvanecare.com
        </li>
        <li class="contact-item website">
          <span class="contact-icon"></span>
          <span>www.<span class="domain">solvanecare</span>.com</span>
        </li>
      </ul>
    </section>
  </article>
</main>
</body>
</html>
```